PTA Meeting Poster

We are looking to create a poster to invite parents of our school to our monthly PTA Meeting.

The copy should include:

PTA Meeting
This Wednesday
8:40am
in the Multi Purpose Room

All Welcome!

```html
<!DOCTYPE html>
<html lang="en">
<head>
<meta charset="UTF-8">
<title>PTA Meeting – This Wednesday</title>
<link rel="stylesheet" href="https://fonts.googleapis.com/css2?family=Fredoka:wght@600;700&family=Federo&display=swap">
<style>
  :root {
    --board-light: #2f7a6d;
    --board-mid: #1d5f55;
    --board-dark: #0f3d37;
    --chalk-white: #ffffff;
    --title-purple-light: #b76bd0;
    --title-purple-dark: #5e1c78;
    --gold-light: #ffe27a;
    --gold-mid: #f2b01e;
    --gold-dark: #b8740a;
    --desk-light: #ecdcb2;
    --desk: #e3cf9f;
    --still-life-top: #8cbf48;
    --still-life-mid: #7d8f52;
    --still-life-base: #a88a55;
  }
  html, body {
    margin: 0;
    padding: 0;
    width: 849px;
    height: 1200px;
    overflow: hidden;
    background: var(--board-dark);
  }
  .poster {
    position: relative;
    width: 849px;
    height: 1200px;
    overflow: hidden;
    font-family: "Federo", "Trebuchet MS", sans-serif;
    color: var(--chalk-white);
  }
  .chalkboard {
    position: absolute;
    inset: 0;
    background: radial-gradient(ellipse at 50% 40%, var(--board-light) 0%, var(--board-mid) 55%, var(--board-dark) 100%);
  }
  .desk {
    position: absolute;
    left: 0;
    right: 0;
    bottom: 0;
    height: 75px;
    background: linear-gradient(180deg, var(--desk-light) 0%, var(--desk) 100%);
  }
  .still-life {
    position: absolute;
    left: 0;
    top: 850px;
    width: 385px;
    height: 320px;
    background: linear-gradient(180deg, var(--still-life-top) 0%, var(--still-life-mid) 50%, var(--still-life-base) 100%);
    clip-path: polygon(118px 5px, 300px 5px, 300px 150px, 340px 150px, 385px 245px, 385px 320px, 0 320px, 0 150px, 118px 150px);
  }
  .title {
    position: absolute;
    left: 0;
    top: 130px;
    width: 849px;
    height: 220px;
  }
  .title text {
    font-family: "Fredoka", "Arial Rounded MT Bold", sans-serif;
    font-weight: 700;
    font-size: 162px;
    paint-order: stroke fill;
    stroke: var(--chalk-white);
    stroke-width: 20px;
    stroke-linejoin: round;
  }
  .rule {
    position: absolute;
    height: 3px;
    background: var(--chalk-white);
    box-shadow: 0 2px 4px rgba(0,0,0,.35);
  }
  .rule--top { left: 158px; width: 519px; top: 378px; }
  .rule--bottom { left: 165px; width: 521px; top: 713px; }
  .details {
    position: absolute;
    left: 0;
    width: 849px;
    top: 410px;
    text-align: center;
    text-shadow: 0 3px 5px rgba(0,0,0,.45);
  }
  .details p { margin: 0; line-height: 1; -webkit-text-stroke: 1.5px var(--chalk-white); }
  .details__day { font-size: 60px; letter-spacing: 1px; }
  .details .details__time { font-size: 94px; margin-top: 4px; -webkit-text-stroke: 3px var(--chalk-white); }
  .details .details__in { font-size: 40px; margin-top: 22px; }
  .details .details__room { font-size: 45px; margin-top: 14px; }
  .welcome {
    position: absolute;
    margin: 0;
    font-size: 80px;
    line-height: 1;
    letter-spacing: 2px;
    white-space: nowrap;
    text-align: center;
    background: linear-gradient(180deg, var(--gold-light) 0%, var(--gold-mid) 50%, var(--gold-dark) 100%);
    -webkit-background-clip: text;
    background-clip: text;
    color: transparent;
    -webkit-text-stroke: 1.5px var(--gold-mid);
    filter: drop-shadow(0 3px 3px rgba(0,0,0,.45));
  }
  .welcome--all { left: 440px; width: 200px; top: 800px; }
  .welcome--word { left: 352px; width: 443px; top: 910px; }
</style>
</head>
<body>
  <main class="poster">
    <div class="chalkboard" role="img" aria-label="Green school chalkboard background"></div>
    <div class="desk"></div>
    <div class="still-life" role="img" aria-label="Green apple and chalk resting on a stack of old books"></div>

    <svg class="title" viewBox="0 0 849 220" aria-label="PTA Meeting">
      <defs>
        <linearGradient id="titleFill" x1="0" y1="0" x2="0" y2="1">
          <stop offset="0" stop-color="#b76bd0"/>
          <stop offset="1" stop-color="#5e1c78"/>
        </linearGradient>
      </defs>
      <text x="424" y="170" text-anchor="middle" fill="url(#titleFill)" textLength="700" lengthAdjust="spacingAndGlyphs">PTA MEETING</text>
    </svg>

    <div class="rule rule--top"></div>
    <section class="details">
      <p class="details__day">THIS WEDNESDAY</p>
      <p class="details__time">8:40AM</p>
      <p class="details__in">IN THE</p>
      <p class="details__room">MULTI PURPOSE ROOM</p>
    </section>
    <div class="rule rule--bottom"></div>

    <p class="welcome welcome--all">ALL</p>
    <p class="welcome welcome--word">WELCOME!</p>
  </main>
</body>
</html>
```